Brell Stone Company Business Cards

Front and Back Business Card - logo and text setup - cool design. I need workable photoshop or illustrator files so I can setup each employee card with design that is created
Updates

Hi everyone, thank you for the great entries. Please no more white and blue cards - there are so many already - black and silver only now please. thanks!

Target Market(s)

Construction Industry - Facility Managers

Industry/Entity Type

Construction

Contact Information for Business Card

I really like contemporary simplistic looks - clean neat....not opposed to seeing some black backrounds

Requirements
Must have
• Logo/website address with design on front only - www.brellstone-example.com (logo attached)
• Back:
• Name/Title/Company Address/Phone/email address
Nice to have
• Cool design
Should not have
• Nothing gimmicky like Fire or Water - since we are a Fire Protection company - it has all been done

```html
<!DOCTYPE html>
<html lang="en">
<head>
<meta charset="utf-8">
<title>Brell Stone Company Business Cards</title>
<link rel="stylesheet" href="https://fonts.googleapis.com/css2?family=Open+Sans:wght@400;600;700;800&display=swap">
<style>
  :root {
    --backdrop: #2a2a2c;
    --card: #050505;
    --silver: #8c8c8c;
    --silver-light: #b8b8b8;
    --text: #f2f2f2;
    --rule: #5a5a5a;
  }
  * { box-sizing: border-box; margin: 0; padding: 0; }
  html, body {
    width: 1200px; height: 960px; overflow: hidden;
    background: var(--backdrop);
    font-family: "Open Sans", Arial, sans-serif;
  }
  .canvas {
    position: relative; width: 1200px; height: 960px;
  }
  .card {
    position: absolute; left: 250px; width: 700px; height: 400px;
    background: var(--card); border-radius: 4px;
    box-shadow: 0 14px 36px rgba(0,0,0,.45);
    overflow: hidden;
  }
  .card-front { top: 60px; }
  .card-back { top: 500px; }

  /* front */
  .front-brand {
    position: absolute; left: 0; right: 0; top: 130px;
    text-align: center;
    font-size: 66px; font-weight: 800; letter-spacing: -1px;
    color: var(--silver);
  }
  .front-url {
    position: absolute; left: 0; right: 0; top: 250px;
    text-align: center;
    font-size: 18px; letter-spacing: 4px; color: var(--silver-light);
  }

  /* back */
  .back-brand {
    position: absolute; left: 40px; top: 40px;
    font-size: 40px; font-weight: 800; letter-spacing: -.5px;
    color: var(--silver);
  }
  .back-rule {
    position: absolute; left: 0; right: 0; top: 150px;
    height: 1px; background: var(--rule);
  }
  .address {
    position: absolute; left: 40px; top: 180px;
    font-size: 15px; line-height: 26px; color: var(--text);
  }
  .person {
    position: absolute; right: 40px; top: 96px; text-align: right;
  }
  .person-name {
    font-size: 24px; font-weight: 700; color: var(--text); line-height: 44px;
  }
  .person-title {
    font-size: 20px; color: var(--text); margin-top: 12px;
  }
  .contacts {
    position: absolute; right: 40px; bottom: 40px;
    list-style: none; text-align: right;
  }
  .contacts li {
    display: flex; justify-content: flex-end; align-items: center; gap: 12px;
    font-size: 15px; line-height: 28px; color: var(--text);
  }
  .contacts svg { width: 16px; height: 16px; fill: none; stroke: var(--text); stroke-width: 1.6; }
</style>
</head>
<body>
<main class="canvas">
  <section class="card card-front">
    <div class="front-brand">Brell Stone</div>
    <div class="front-url">www.brellstone-example.com</div>
  </section>

  <section class="card card-back">
    <div class="back-brand">Brell Stone</div>
    <div class="person">
      <div class="person-name">Dana Whitfield</div>
      <div class="person-title">President</div>
    </div>
    <div class="back-rule"></div>
    <address class="address" style="font-style:normal">
      48 Harbor Point Road<br>
      Millbrook, NY 10000
    </address>
    <ul class="contacts">
      <li>(555) 014-2290
        <svg viewBox="0 0 16 16" aria-hidden="true"><path d="M4 1.5l2.5 3-1.5 1.5c.8 2 2.5 3.7 4.5 4.5l1.5-1.5 3 2.5-1.5 2.5C7 14 2 9 1.5 3z"/></svg>
      </li>
      <li>info@brellstone-example.com
        <svg viewBox="0 0 16 16" aria-hidden="true"><rect x="1.5" y="3.5" width="13" height="9"/><path d="M1.5 3.5l6.5 5 6.5-5"/></svg>
      </li>
      <li>www.brellstone-example.com
        <svg viewBox="0 0 16 16" aria-hidden="true"><circle cx="8" cy="8" r="6.5"/><ellipse cx="8" cy="8" rx="3" ry="6.5"/><path d="M1.5 8h13"/></svg>
      </li>
    </ul>
  </section>
</main>
</body>
</html>
```